Smart Routing SaaS needs a magic web design

We need a web design that focuses in the UX and conveys the idea of doing magic through our software. The company name is Brantiq and it is a word game about wow and slip... we are a software as a service B2B that helps companies automate dispatches and routes for their delivery guys to deliver goods to the customers. Think of it as an zephyr software applicable to your own fleet or third party fleets that can be used for example in a supermarket. That way the final user (buyer of the supermarket) knows where the parcel is, if it is leaving the store, if it is on its way, how long will it take to arrive, who is the delivery guy, etc... Brantiq's symbol is an owl. Think of it as the movie The Lanternkeep: Autumn's Oath, Queen Odalie had an owl mask and the ice owl who was her eyes on the field... that is the idea I want to convey through this software. It is the eyes for the business and the eyes for the final user. The software is comprised of a web platform (for the business with the fleet to manage) and the driver's application. The final customer receives the real time tracking information through SMS and email. The design should communicate magic through the use of the software... You can see some info on the existing webpage... which is very cold and dull... no life in it brantiq.example.. Use of gifs is desirable.

Text that can be used on the cover to convey main idea:

High end technology
We take care of your delivery management

The software that brings visibility and smartness to your deliveries through automated dispatches and smart routings
Our expertise: A Delightful Customer Experience of Deliveries

Target Market(s)

Professionals and businesses of all types with a delivery of any kind (supermarkets, pharmacies, restaurants, moving services, fleets, home services, deliveries, supply chain, field sales...)
Please look at competition webpages:
www.pathkit7.example
www.movra.example
www.trekly.example
vantacor.example
quickbarn.example
zephyr dash

Industry/Entity Type

Business Software

Coding

Coded - Design and coding required

Number of Pages Required

5+ page

Font styles to use
Other font styles liked:
• Modulus and Trade Gothic Ltd

Requirements
Must have
• MUST HAVE A D3JS LIKE:
• http://grafnode.example/jterran/5518302
• http://jterran.codepages.example/d3/talk/20111116/force-collapsible.html
• https://plinthware.example/hugo/fisheye/
• http://movingcharts.example/lab/d3-tree/
• A great magic capturing Homepage that conveys the main idea of what we are. A software that will help you manage your people on field who are getting something to the end customer (who will be aware of the live parcel status through SMS/ email notifications), we live in the cloud... no need of implementation fees, there is a free demo. Right now the webpage has an animation. Maybe a picture with a video on it could be something nice, or something that moves... take a look at zephyr dash. The main idea of the page should send the idea of something magic... use the owl... something that flies.
• The page must have gifs here and there... never stop the idea of a swift magic going on... efficiency on the logistics management of the company... happy customers.
• Parallax... I love parallax.
Nice to have
• The webpage may be telling a story... first what are we and what we do... how it works, who is our market, the benefits, hard facts on efficiency... please take a look at the current webpage www.brantiq.example to get more info but make it beautiful.
• A phrase here and there of why they need our service
Should not have
• I want to change the current idea of the webpage that the software aims only to manage fleets for home delivery... we are NOT a home delivery only management system. We can make any company's logistics "fly".
• I dont want to see dullness in the webpage, I am looking for a soul.

```html
<!DOCTYPE html>
<html lang="es">
<head>
<meta charset="utf-8">
<title>Brantiq — Software de alta tecnología</title>
<link rel="stylesheet" href="https://fonts.googleapis.com/css2?family=Roboto+Condensed:wght@300;400;700&family=Raleway:wght@400;500&display=swap">
<style>
:root{
  --cyan:#15a9c9;
  --cyan-deep:#0b8fb0;
  --cyan-light:#4fd0e6;
  --yellow:#f7b52c;
  --yellow-deep:#f39c12;
  --ink:#3d3d3d;
  --grey-text:#8a8a8a;
  --grey-soft:#bdbdbd;
  --grey-band:#e9e9e9;
  --ring:#dcdcdc;
  --fact:#cccccc;
  --white:#ffffff;
  --black:#0d0d0d;
}
*{margin:0;padding:0;box-sizing:border-box}
html,body{width:1200px;height:2757px;overflow:hidden;background:var(--white)}
body{position:relative;font-family:"Raleway",sans-serif;color:var(--ink)}
.center{position:absolute;left:0;width:1200px;text-align:center;white-space:nowrap}
.col{position:absolute;width:300px;text-align:center}

/* header */
.site-header{position:absolute;left:0;top:0;width:1200px;height:92px;background:var(--white);z-index:3}
.brand{position:absolute;left:122px;top:26px;display:flex;align-items:center;gap:10px;font-family:"Raleway",sans-serif;font-weight:500;font-size:36px;color:var(--cyan);line-height:40px}
.brand-dot{width:12px;height:12px;border-radius:50%;background:var(--cyan)}
.main-nav{position:absolute;top:38px;font-family:"Roboto Condensed",sans-serif;font-size:17px;color:var(--ink);letter-spacing:.2px}
.main-nav span{position:absolute;white-space:nowrap;transform:translateX(-50%)}

/* hero: a living, shifting light to suggest swift magic */
@keyframes drift{0%{background-position:0% 50%}50%{background-position:100% 50%}100%{background-position:0% 50%}}
.hero{position:absolute;left:0;top:92px;width:1200px;height:524px;
  background:linear-gradient(100deg,#0e9cc0 0%,#27b9d6 25%,#6ad8ea 45%,#19a8cb 70%,#0e9cc0 100%);
  background-size:220% 100%;animation:drift 14s ease-in-out infinite;
  clip-path:polygon(0 0,1200px 0,1200px 389px,0 524px)}
.hero-title{top:154px;font-family:"Roboto Condensed",sans-serif;font-weight:300;font-size:42px;color:var(--white);letter-spacing:.5px;z-index:2}
.hero-sub{top:214px;font-family:"Roboto Condensed",sans-serif;font-weight:300;font-size:24px;color:var(--white);letter-spacing:.4px;z-index:2}
.product-demo{position:absolute;left:272px;top:279px;width:674px;height:362px;border-radius:16px 16px 6px 6px;
  background:linear-gradient(180deg,#e6e6e6,#c9c9c9);z-index:2}
.product-screen{position:absolute;left:24px;top:24px;width:626px;height:300px;background:linear-gradient(135deg,#f3f3f3,#e2e6e8)}
.play-icon{position:absolute;left:578px;top:424px;z-index:3}

/* expertise */
.expert-a{top:686px;font-size:26px;font-family:"Roboto Condensed",sans-serif;font-weight:300;color:var(--grey-text)}
.expert-b{top:722px;font-size:28px;font-family:"Roboto Condensed",sans-serif;font-weight:300;color:var(--ink)}

/* how it works */
.section-title{font-family:"Roboto Condensed",sans-serif;font-weight:400;font-size:32px;color:var(--cyan)}
.rule{position:absolute;height:1px;background:var(--ring)}
.step-visual{position:absolute;width:210px;height:210px;border-radius:50%;border:9px solid var(--ring);background:#f0f0f0}
.step-num{position:absolute;width:44px;height:44px;border-radius:50%;background:var(--yellow);color:var(--white);
  font-family:"Roboto Condensed",sans-serif;font-size:26px;line-height:44px;text-align:center}
.step-text{font-size:14.5px;line-height:22px;color:var(--grey-text)}

/* market */
.market{position:absolute;left:0;top:1270px;width:1200px;height:623px;background:var(--grey-band)}
.market-kicker{top:1314px;font-family:"Roboto Condensed",sans-serif;font-weight:700;font-size:24px;color:var(--cyan)}
.market-title{top:1343px;font-family:"Roboto Condensed",sans-serif;font-size:35px;color:var(--ink)}
.market-icon{position:absolute;width:132px;height:132px;border-radius:50%;background:var(--cyan);border:6px solid var(--white);
  display:flex;align-items:center;justify-content:center}
.market-label{font-size:15.5px;line-height:22px;color:var(--ink);letter-spacing:.3px}

/* growth band */
.growth{position:absolute;left:0;top:1893px;width:1200px;height:318px;
  background:linear-gradient(100deg,#f9c545 0%,#f6b42a 30%,#fbd063 50%,#f2a318 100%);
  background-size:220% 100%;animation:drift 16s ease-in-out infinite}
.growth-a{top:2000px;font-family:"Roboto Condensed",sans-serif;font-weight:700;font-size:41px;color:var(--white)}
.growth-b{top:2048px;font-family:"Roboto Condensed",sans-serif;font-weight:400;font-size:33px;color:var(--white)}

/* facts */
.facts-title{top:2251px}
.fact-num{font-family:"Roboto Condensed",sans-serif;font-weight:700;font-size:74px;color:var(--fact);line-height:80px}
.fact-label{font-size:15.5px;line-height:22px;color:var(--ink)}

/* footer */
.site-footer{position:absolute;left:0;top:2580px;width:1200px;height:177px;background:var(--black);color:var(--white)}
.footer-nav{position:absolute;top:40px;font-family:"Roboto Condensed",sans-serif;font-weight:700;font-size:20px}
.footer-nav span{position:absolute;transform:translateX(-50%);white-space:nowrap}
.copyright{top:70px;font-size:13.5px;color:#cfcfcf}
.social{position:absolute;top:103px;width:30px;height:30px;border-radius:50%;border:1.5px solid var(--white)}
</style>
</head>
<body>

<header class="site-header">
  <div class="brand"><span class="brand-dot"></span>Brantiq</div>
  <nav class="main-nav">
    <span style="left:706px">PLATAFORMA</span>
    <span style="left:836px">NOSOTROS</span>
    <span style="left:945px">CONTACTO</span>
    <span style="left:1036px">LOGIN</span>
  </nav>
</header>

<section class="hero" role="img" aria-label="Fotografía de un repartidor en tono cian"></section>
<h1 class="center hero-title">SOFTWARE DE ALTA TECNOLOGÍA</h1>
<p class="center hero-sub">QUE HACE VOLAR LA LOGÍSTICA DE TU NEGOCIO</p>

<div class="product-demo">
  <div class="product-screen" role="img" aria-label="Captura de la plataforma con mapa de rutas y lista de pedidos"></div>
</div>
<svg class="play-icon" width="70" height="70" viewBox="0 0 70 70" aria-label="Reproducir video">
  <circle cx="35" cy="35" r="31" fill="rgba(255,255,255,.85)" stroke="#111" stroke-width="4"/>
  <path d="M28 21 L50 35 L28 49 Z" fill="none" stroke="#111" stroke-width="4" stroke-linejoin="round"/>
</svg>

<p class="center expert-a">SOMOS EXPERTOS EN</p>
<p class="center expert-b">ADMINISTRACIÓN LOGÍSTICA Y ENTREGAS DE TODO TIPO CON:</p>

<div class="rule" style="left:132px;top:847px;width:308px"></div>
<div class="rule" style="left:760px;top:847px;width:288px"></div>
<h2 class="center section-title" style="top:826px">¿CÓMO FUNCIONA?</h2>

<div class="step-visual" style="left:139px;top:893px" role="img" aria-label="Ilustración de formulario de pedido"></div>
<div class="step-visual" style="left:378px;top:893px" role="img" aria-label="Ilustración de mapa con ruta óptima"></div>
<div class="step-visual" style="left:617px;top:893px" role="img" aria-label="Ilustración de mapa con ruta del mensajero"></div>
<div class="step-visual" style="left:854px;top:893px" role="img" aria-label="Ilustración de mensajes de seguimiento"></div>
<div class="step-num" style="left:222px;top:1068px">1</div>
<div class="step-num" style="left:461px;top:1068px">2</div>
<div class="step-num" style="left:700px;top:1068px">3</div>
<div class="step-num" style="left:937px;top:1068px">4</div>
<p class="col step-text" style="left:94px;top:1122px">Ingresa las órdenes<br>manualmente o desde<br>un archivo CSV</p>
<p class="col step-text" style="left:333px;top:1122px">El sistema se encarga<br>de asignar al mensajero y<br>generar la ruta óptima</p>
<p class="col step-text" style="left:572px;top:1122px">Se despacha el pedido<br>a través de la aplicación<br>del mensajero</p>
<p class="col step-text" style="left:809px;top:1122px">Deleita a tus clientes con<br>visibilidad en tiempo real<br>de su pedido</p>

<section class="market"></section>
<p class="center market-kicker">ESTAMOS DIRIGIDOS A</p>
<h2 class="center market-title">NEGOCIOS DE PEDIDOS</h2>

<div class="market-icon" style="left:169px;top:1419px"><svg width="64" height="64" viewBox="0 0 64 64" fill="none" stroke="#fff" stroke-width="4" stroke-linejoin="round"><path d="M8 26h48l-6 26H14z"/><path d="M20 26l8-14M44 26l-8-14M24 32v14M32 32v14M40 32v14"/></svg></div>
<div class="market-icon" style="left:403px;top:1419px"><svg width="64" height="64" viewBox="0 0 64 64" fill="none" stroke="#fff" stroke-width="4"><circle cx="32" cy="34" r="14"/><path d="M9 10v14a3 3 0 0 0 6 0V10M12 24v32M54 10c-6 4-6 18 0 22v24"/></svg></div>
<div class="market-icon" style="left:634px;top:1419px"><svg width="64" height="64" viewBox="0 0 64 64"><g transform="rotate(-45 32 32)"><rect x="8" y="21" width="48" height="22" rx="11" fill="#fff"/><rect x="32" y="24" width="21" height="16" rx="8" fill="#15a9c9"/></g></svg></div>
<div class="market-icon" style="left:866px;top:1419px"><svg width="70" height="64" viewBox="0 0 70 64" fill="none" stroke="#fff" stroke-width="3.5" stroke-linejoin="round"><path d="M6 10h24v22H6zM30 18h8l6 8v6H30"/><path d="M24 34h26v18H24zM50 40h8l6 7v5H50"/><circle cx="32" cy="54" r="4"/><circle cx="56" cy="54" r="4"/></svg></div>

<p class="col market-label" style="left:85px;top:1564px">ENTREGA DE<br>SUPERMERCADOS</p>
<p class="col market-label" style="left:319px;top:1564px">ENTREGA DE<br>RESTAURANTES</p>
<p class="col market-label" style="left:550px;top:1564px">ENTREGA DE<br>FARMACIAS</p>
<p class="col market-label" style="left:782px;top:1564px">MANEJO DE<br>FLOTILLAS</p>

<div class="market-icon" style="left:169px;top:1638px"><svg width="64" height="64" viewBox="0 0 64 64" fill="none" stroke="#fff" stroke-width="4" stroke-linejoin="round"><path d="M10 8h44l4 14H6z"/><path d="M10 22v34h44V22M26 56V38h12v18"/></svg></div>
<div class="market-icon" style="left:403px;top:1638px"><svg width="64" height="64" viewBox="0 0 64 64" fill="none" stroke="#fff" stroke-width="4" stroke-linejoin="round"><path d="M4 16h34v28H4zM38 24h12l10 10v10H38"/><circle cx="16" cy="46" r="5" fill="#15a9c9"/><circle cx="48" cy="46" r="5" fill="#15a9c9"/></svg></div>
<div class="market-icon" style="left:634px;top:1638px"><svg width="64" height="64" viewBox="0 0 64 64" fill="none" stroke="#fff" stroke-width="4" stroke-linejoin="round"><path d="M4 10h10l8 32h30l6-22H18"/><circle cx="26" cy="52" r="4"/><circle cx="48" cy="52" r="4"/></svg></div>
<div class="market-icon" style="left:866px;top:1638px"><svg width="64" height="64" viewBox="0 0 64 64" fill="none" stroke="#fff" stroke-width="4" stroke-linejoin="round"><path d="M4 18h36v24H4zM40 26h12l8 8v8H40"/><circle cx="16" cy="46" r="5" fill="#15a9c9"/><circle cx="48" cy="46" r="5" fill="#15a9c9"/></svg></div>

<p class="col market-label" style="left:85px;top:1783px">SERVICIOS<br>DEL HOGAR</p>
<p class="col market-label" style="left:319px;top:1783px">MUDANZAS</p>
<p class="col market-label" style="left:550px;top:1783px">COMERCIO<br>ELECTRÓNICO</p>
<p class="col market-label" style="left:782px;top:1783px">ZEPHYR DE X</p>

<section class="growth" role="img" aria-label="Fotografía de una persona trabajando, en tono amarillo"></section>
<h2 class="center growth-a">BUSCAMOS HACER VOLAR TU NEGOCIO</h2>
<p class="center growth-b">DE FORMA EFICIENTE CON</p>

<h2 class="center section-title facts-title">DATOS DUROS</h2>
<p class="col fact-num" style="left:104px;top:2356px">27%</p>
<p class="col fact-num" style="left:337px;top:2356px">35%</p>
<p class="col fact-num" style="left:570px;top:2356px">31%</p>
<p class="col fact-num" style="left:806px;top:2356px">29%</p>
<p class="col fact-label" style="left:104px;top:2448px">Reducción en tiempos<br>de entrega</p>
<p class="col fact-label" style="left:337px;top:2448px">Aumento de pedidos</p>
<p class="col fact-label" style="left:570px;top:2448px">Aumento en la productividad<br>del personal</p>
<p class="col fact-label" style="left:806px;top:2448px">Reducción en entregas<br>fallidas</p>

<footer class="site-footer">
  <nav class="footer-nav">
    <span style="left:428px">PLATAFORMA</span>
    <span style="left:568px">NOSOTROS</span>
    <span style="left:696px">CONTACTO</span>
    <span style="left:805px">LOGIN</span>
  </nav>
  <p class="center copyright">© 2016 Company Name &nbsp;All right reserved</p>
  <span class="social" style="left:536px"></span>
  <span class="social" style="left:569px"></span>
  <span class="social" style="left:604px"></span>
  <span class="social" style="left:639px"></span>
</footer>

</body>
</html>
```